Fernhale Business Card Design

We are looking for a fresh business card design for our new logo. We would like a business card that is unique but friendly. We are in the window coverings business offering blinds, shutters and shades for homes.

Target Market(s)

Targeting the end-consumer

Industry/Entity Type

Business

Requirements
Must have
• Must have a dedicates space for a photo of our sales person. Must contain our new logo (attached).

```html
<!DOCTYPE html>
<html lang="en">
<head>
<meta charset="utf-8">
<title>Fernhale Business Card</title>
<link href="https://fonts.googleapis.com/css2?family=Roboto:wght@400;500&family=Roboto+Condensed:wght@500&display=swap" rel="stylesheet">
<style>
  :root {
    --bg: #e6e3df;
    --card-front: #f3f3f3;
    --card-back: #76767b;
    --frame-dark: #7a7a7a;
    --frame-light: #ffffff;
    --accent: #7cb342;
    --text: #4a4a4a;
    --text-muted: #6e6e6e;
    --photo: #c9c9cc;
  }
  * { margin: 0; padding: 0; box-sizing: border-box; }
  html, body { width: 1200px; height: 960px; overflow: hidden; }
  body {
    background: var(--bg);
    font-family: "Roboto", Arial, sans-serif;
    position: relative;
  }
  .card {
    position: absolute;
    width: 600px;
    height: 343px;
    box-shadow: 0 2px 6px rgba(0,0,0,0.25);
  }
  .card-front { left: 314px; top: 113px; background: var(--card-front); }
  .card-back { left: 311px; top: 472px; background: var(--card-back); }
  .card-frame { position: absolute; left: 0; top: 0; }
  .staff-photo {
    position: absolute;
    left: 259px; top: 67px;
    width: 82px; height: 109px;
    border-radius: 8px;
    border: 1.5px solid #333;
    background: linear-gradient(180deg, #d4d4d7, var(--photo));
  }
  .front-text {
    position: absolute;
    left: 0; right: 0;
    text-align: center;
    color: var(--text);
  }
  .person-name {
    top: 183px;
    font-family: "Roboto Condensed", "Roboto", sans-serif;
    font-weight: 500;
    font-size: 21px;
    color: var(--accent);
    letter-spacing: 0.3px;
  }
  .person-role {
    top: 208px;
    font-size: 15px;
    color: var(--text-muted);
  }
  .address { top: 234px; font-size: 14px; }
  .contacts { top: 255px; font-size: 14px; white-space: nowrap; }
  .web { top: 275px; font-size: 14px; }
  .label { color: var(--accent); font-weight: 500; }
  .brand {
    position: absolute;
    left: 124px; top: 130px;
    display: flex; align-items: center; gap: 18px;
  }
  .brand-mark {
    width: 70px; height: 70px;
    border: 3px solid var(--frame-light);
    border-radius: 6px;
  }
  .brand-name {
    font-size: 50px;
    font-weight: 400;
    color: var(--frame-light);
  }
  .back-web {
    position: absolute;
    left: 0; right: 0; top: 287px;
    text-align: center;
    color: var(--frame-light);
    font-size: 14px;
    letter-spacing: 6px;
  }
</style>
</head>
<body>
  <section class="card card-front">
    <svg class="card-frame" width="600" height="343" aria-hidden="true">
      <path d="M64 12 H580 a6 6 0 0 1 6 6 V268 a62 62 0 0 1 -62 62 H20 a6 6 0 0 1 -6 -6 V74 a62 62 0 0 1 50 -62 Z"
            fill="none" stroke="var(--frame-dark)" stroke-width="2"/>
    </svg>
    <div class="staff-photo" role="img" aria-label="Photo of the sales person"></div>
    <p class="front-text person-name">DANA ELLERY</p>
    <p class="front-text person-role">CEO/FOUNDER</p>
    <p class="front-text address">4120 Willowbend Road, Juneau, Alaska 34580</p>
    <p class="front-text contacts">
      <span class="label">P:</span> 555 210 4471
      <span class="label">M:</span> 555 318 6620
      <span class="label">F:</span> 555 742 0913
      <span class="label">E:</span> name@fernhale.com
    </p>
    <p class="front-text web"><span class="label">W:</span> www.fernhale.com</p>
  </section>

  <section class="card card-back">
    <svg class="card-frame" width="600" height="343" aria-hidden="true">
      <path d="M64 12 H580 a6 6 0 0 1 6 6 V268 a62 62 0 0 1 -62 62 H20 a6 6 0 0 1 -6 -6 V74 a62 62 0 0 1 50 -62 Z"
            fill="none" stroke="var(--frame-light)" stroke-width="2"/>
    </svg>
    <div class="brand">
      <span class="brand-mark" aria-hidden="true"></span>
      <span class="brand-name">Fernhale</span>
    </div>
    <p class="back-web">www.fernhale.com</p>
  </section>
</body>
</html>
```